Brightmoor - a website to encourage people to spend time in nature

I have a squarespace site with some content on it but the squarespace template doesn't completely suit my needs, I keep fiddling with the template but actually I need some professional help to get it looking the way I want and with the right 'mood'.
The website is for "Brightmoor" - it will be a blog where I write about the importance of nature for good health. I also want to use the website to market services such as outdoor coaching, retreats and walking workshops.
This has been in my head for a LONG time and I currently only use instagram for micro-blogs but it's time for me to get this moving. I've previously engaged other designers on branding for it but they just didn't get it quite the way that I wanted it and I wasn't completely happy with the results. It's been a process for me as to what I want but in the meantime I just didn't come back to the design aspect of it now. I'm looking for a designer who understands the purpose of the website, the ethos and can help me realise this into a design that's clean, clear and simple.

Please note that I have a domain (brightmoor.org) and a lot of content drafted on squarespace already. I have published it with password protection - password is brightmoor2020 - it still has some of the original template on it, but does have some content. Don't take it as anything to follow in particular, i am looking for fresh eyes and fresh ideas.

Target Market(s)

There are three main groups that I want to target - people who are suffering from stress and anxiety, people who treat them and parents who want to get their kids outside (thereby preventing stress and anxiety)

Contact Information for Business Card

Joan Petrie
Brightmoor
Telephone +44 7700 900417
brightmoor@mailvane.com

Logo Text

Brightmoor - if that. I have an idea that the logo should have a leaf on it somewhere, or maybe just be a leaf.

Coding

Coded - Design and coding required

Number of Pages Required

5+ page

Font styles to use
Serif
Sans Serif

Colors
add136
33b8a4
34a6d7
3377b5

Requirements
Must have
• Space for lots of images. The ability for me to edit the pages if I need to. Be user friendly. Look beautiful.
• For an idea of the images I use and the content I'm interested in writing about have a look at @brightmoor on instagram.
• That pop up about cookies so I am complying with data laws.
Should not have
• Must not be too 'busy' I'd like to avoid too much movement.

```html
<!DOCTYPE html>
<html lang="en">
<head>
<meta charset="utf-8">
<title>Brightmoor – Home</title>
<link rel="stylesheet" href="https://fonts.googleapis.com/css2?family=Poppins:wght@400;500;600;700&family=Lato:wght@400;700&display=swap">
<style>
:root{
  --stage:#e5e5e5;
  --blue:#3377b5;
  --teal:#33b8a4;
  --sky:#34a6d7;
  --ink:#333;
  --muted:#555;
  --footer:#232323;
  --white:#fff;
}
*{box-sizing:border-box;margin:0;padding:0}
html,body{width:1085px;height:1200px;overflow:hidden;background:var(--stage)}
body{position:relative;font-family:'Lato',sans-serif}
.screen{position:absolute;width:620px;height:1735px;transform-origin:0 0;transform:scale(.5952);background:var(--white);overflow:hidden;box-shadow:0 2px 8px rgba(0,0,0,.12)}
.screen--home{left:114px;top:83px}
.screen--consent{left:562px;top:87.5px}
.abs{position:absolute}
.heading{font-family:'Poppins',sans-serif;font-weight:700}
.btn{position:absolute;background:var(--teal);color:var(--white);font-family:'Poppins',sans-serif;font-weight:600;display:flex;align-items:center;justify-content:center}

/* hero */
.hero{left:0;top:0;width:620px;height:324px;background:linear-gradient(160deg,#2f3f22 0%,#4e6b2a 35%,#7aa13a 55%,#3d5424 80%,#26331a 100%)}
.brand{display:flex;align-items:center;gap:7px;color:var(--white);font-family:'Poppins',sans-serif;font-weight:700;font-size:14px}
.brand-dot{width:22px;height:22px;border-radius:50%;background:var(--white)}
.nav{left:244px;top:22px;display:flex;gap:11px;font-family:'Poppins',sans-serif;font-size:8px;color:var(--white)}
.nav .active{color:var(--sky)}
.social{left:450px;top:24px;display:flex;gap:12px}
.social span{width:7px;height:7px;border-radius:50%;background:var(--white)}
.hero-title{left:46px;top:96px;font-size:29px;color:var(--white)}
.hero-text{left:46px;top:133px;width:194px;font-size:9.4px;line-height:16.6px;color:var(--white);text-align:justify}

/* about band */
.about{left:0;top:324px;width:620px;height:168px;background:var(--blue);color:var(--white)}
.about-title{left:46px;top:26px;font-size:16px;font-weight:600}
.about-lead{left:46px;top:56px;width:205px;font-size:11.5px;line-height:21.4px;text-align:justify}
.about-lead u{text-underline-offset:2px}
.about-body{left:337px;top:33px;width:238px;font-size:9.2px;line-height:16.7px;text-align:justify}

/* services */
.svc-title{font-size:21px;color:var(--blue);letter-spacing:.2px}
.svc-text{width:245px;font-size:9.8px;line-height:18.5px;color:var(--muted);text-align:justify}
.photo{position:absolute;width:222px;height:195px}
.photo--walk{left:352px;top:528px;background:linear-gradient(180deg,#c6cbcc 0%,#b4b9b2 40%,#6b5e3e 62%,#5a4c3a 100%)}
.photo--bloom{left:46px;top:759px;background:radial-gradient(circle at 40% 45%,#f6c8d8 0%,#e4789e 50%,#c0406e 100%)}
.photo--stream{left:352px;top:990px;background:linear-gradient(180deg,#3b4a26 0%,#5c6a3a 45%,#76756c 70%,#54534c 100%)}
.btn--sm{width:80px;height:26px;font-size:9.5px}

/* quote */
.quote-band{left:0;top:1222px;width:620px;height:248px;background:linear-gradient(180deg,#4c5638 0%,#3a3f36 45%,#5a4f8a 75%,#4a3f80 100%)}
.quote{left:64px;top:47px;width:490px;font-family:'Poppins',sans-serif;font-size:14.2px;letter-spacing:-.25px;line-height:24px;color:var(--white);text-align:justify;text-align-last:center}
.quote-by{left:0;top:198px;width:620px;text-align:center;font-family:'Poppins',sans-serif;font-weight:700;font-size:11.5px;color:var(--white)}

/* signup */
.signup-title{left:46px;top:1497px;width:210px;font-family:'Poppins',sans-serif;font-size:15px;line-height:24px;color:#222;text-align:justify}
.signup-note{left:337px;top:1503px;width:238px;font-size:6.5px;line-height:13px;color:#222}
.signup-input{left:337px;top:1537px;width:163px;height:27px;border:1px solid #bbb;font-size:6.5px;color:#444;padding:10px 8px}
.btn--signup{left:507px;top:1537px;width:67px;height:27px;background:var(--blue);font-size:9px}

/* footer */
.footer{left:0;top:1612px;width:620px;height:123px;background:var(--footer);color:var(--white)}
.footer .brand{font-size:10.5px;gap:6px}
.footer .brand-dot{width:16px;height:16px;background:var(--teal)}
.footer-addr{left:46px;top:50px;font-size:7.5px;line-height:14px}
.footer-copy{left:46px;top:99px;font-size:7.5px}
.footer-col{font-size:7px;line-height:16.6px}
.footer-col h4{font-family:'Poppins',sans-serif;font-weight:600;font-size:8px;margin-bottom:4px}

/* consent */
.dim{left:0;top:0;width:620px;height:1735px;background:rgba(0,0,0,.72)}
.cookie-modal{left:129px;top:181px;width:360px;height:288px;background:#f6f6f6;box-shadow:0 3px 10px rgba(0,0,0,.4);text-align:center;font-family:'Poppins',sans-serif;color:#222}
.cookie-art{left:129px;top:19px;width:100px;height:100px;border-radius:50%;background:radial-gradient(circle at 40% 40%,#c27e57 0%,#a05f3c 100%)}
.cookie-close{left:332px;top:17px;width:11px;height:10px;background:#111;display:flex;align-items:center;justify-content:center}
.cookie-text{left:72px;top:140px;width:216px;font-size:12px;line-height:20px}
.btn--okay{left:115px;top:209px;width:129px;height:31px;background:var(--blue);font-size:12px;box-shadow:0 2px 3px rgba(0,0,0,.3)}
.cookie-more{left:0;top:251px;width:360px;font-size:11.5px}
</style>
</head>
<body>

<!-- Home page -->
<section class="screen screen--home">
  <div class="abs hero" role="img" aria-label="Sunlit forest path through green grass between trees"></div>
  <div class="abs brand" style="left:46px;top:20px"><span class="brand-dot"></span>BRIGHTMOOR</div>
  <nav class="abs nav"><span class="active">Home</span><span>About Us</span><span>Services</span><span>Contact Us</span></nav>
  <div class="abs social"><span></span><span></span><span></span></div>
  <div class="btn" style="left:512px;top:17px;width:63px;height:22px;font-size:8px;font-weight:500">Take Action</div>
  <h1 class="abs heading hero-title">BRIGHTMOOR</h1>
  <p class="abs hero-text">This is a programme that we believe works well in a number of settings - particularly GP surgeries, colleges and workplaces.</p>
  <div class="btn" style="left:46px;top:194px;width:97px;height:32px;font-size:11.5px">Get Started</div>

  <div class="abs about">
    <h2 class="abs about-title heading" style="font-weight:600">BRIGHTMOOR ABOUT US</h2>
    <p class="abs about-lead">Our aim is to help people connect with nature as a means to feeling better. We do this in a number of ways. <u>Find out more below.</u></p>
    <p class="abs about-body">The focus of Brightmoor is on people. Making people feel better through time spent in nature. Making the world a better place because the people in it are happier. But the natural by-product of spending time in nature and one of the behind-the-scenes motivator to get people into nature is environmental in the conventional sense of the world.</p>
  </div>

  <h2 class="abs heading svc-title" style="left:46px;top:530px">WALKING WORKSHOPS</h2>
  <p class="abs svc-text" style="left:46px;top:561px">Brightmoor Walking is an initiative aimed at getting people back into nature in the most gentlest of ways - by taking a walk with friends in the great outdoors. The concept is simple - schedule a walk outside, once a week with two or three other people. That's it. Sometimes the best things are the simplest and here's why this works.</p>
  <div class="btn btn--sm" style="left:46px;top:680px">Read more</div>
  <div class="photo photo--walk" role="img" aria-label="Person walking along a wooden boardwalk across moorland"></div>

  <div class="photo photo--bloom" role="img" aria-label="Pink cherry blossom in full bloom"></div>
  <h2 class="abs heading svc-title" style="left:329px;top:767px">RETREATS</h2>
  <p class="abs svc-text" style="left:329px;top:797px">Sometimes you just need to get away from it all. And that's where Brightmoor retreats come in. Our retreats are based at Hollyglen Cottage located at the foot of the Mourne Mountains in beautiful Northern Ireland. Typically 2/3 days that involve restoring your connection to the natural world in stunning surroundings.</p>
  <div class="btn btn--sm" style="left:328px;top:918px">Read more</div>

  <h2 class="abs heading svc-title" style="left:46px;top:993px">OUTDOOR COACHING</h2>
  <p class="abs svc-text" style="left:46px;top:1024px;line-height:19.5px">Only one thing better than coaching and that's coaching in the great outdoors. We believe that being out in nature gives you a greater sense of perspective when working through issues and figuring out life's path. We are part of nature, not apart from it. We are ofWe can provide copy for internal publications.</p>
  <div class="btn btn--sm" style="left:46px;top:1150px">Read more</div>
  <div class="photo photo--stream" role="img" aria-label="Child in a red coat and a small dog by a rocky woodland stream"></div>

  <div class="abs quote-band" role="img" aria-label="Woodland floor carpeted with bluebells">
    <p class="abs quote">“I had had a lot of thoughts about creating Brightmoor for a while. No real direction or goal but just an inclination to create a place to gather resources to gather thoughts and demonstrate how to enjoy the great outdoors to improve your life. What turned the thoughts of what to do from thoughts to action came from an unlikely event”</p>
    <p class="abs quote-by">-Ellis Markham to the Town Hall.</p>
  </div>

  <h3 class="abs signup-title" style="font-weight:400">Let'S Meet Up In Real Life To The Importance Of Nature For Good Health.</h3>
  <p class="abs signup-note">Sign up to be the first to know about In sit amet felis malesuada, feugiat purus eget, varius mi. Nulla lectus ante, consequat</p>
  <div class="abs signup-input">Enter address</div>
  <div class="btn btn--signup">Sign up</div>

  <footer class="abs footer">
    <div class="abs brand" style="left:46px;top:20px"><span class="brand-dot"></span>BRIGHTMOOR.</div>
    <p class="abs footer-addr">48 Fernhill Lane<br>Newcastle, BT33 0AB<br>(555) 555-5555</p>
    <p class="abs footer-copy">© 2020 Brightmoor. All rights reserved</p>
    <div class="abs footer-col" style="left:434px;top:24px"><h4>QUICKS LINKS</h4>Home<br>About Us<br>Services<br>Contact Us</div>
    <div class="abs footer-col" style="left:536px;top:24px"><h4>FOLLOW</h4>Leafnote<br>Pathlink<br>Moorpage</div>
  </footer>
</section>

<!-- Home page with cookie consent -->
<section class="screen screen--consent">
  <div class="abs hero" role="img" aria-label="Sunlit forest path through green grass between trees"></div>
  <div class="abs brand" style="left:46px;top:20px"><span class="brand-dot"></span>BRIGHTMOOR</div>
  <nav class="abs nav"><span class="active">Home</span><span>About Us</span><span>Services</span><span>Contact Us</span></nav>
  <div class="abs social"><span></span><span></span><span></span></div>
  <div class="btn" style="left:512px;top:17px;width:63px;height:22px;font-size:8px;font-weight:500">Take Action</div>
  <h1 class="abs heading hero-title">BRIGHTMOOR</h1>
  <p class="abs hero-text">This is a programme that we believe works well in a number of settings - particularly GP surgeries, colleges and workplaces.</p>
  <div class="btn" style="left:46px;top:194px;width:97px;height:32px;font-size:11.5px">Get Started</div>

  <div class="abs about">
    <h2 class="abs about-title heading" style="font-weight:600">BRIGHTMOOR ABOUT US</h2>
    <p class="abs about-lead">Our aim is to help people connect with nature as a means to feeling better. We do this in a number of ways. <u>Find out more below.</u></p>
    <p class="abs about-body">The focus of Brightmoor is on people. Making people feel better through time spent in nature. Making the world a better place because the people in it are happier. But the natural by-product of spending time in nature and one of the behind-the-scenes motivator to get people into nature is environmental in the conventional sense of the world.</p>
  </div>

  <h2 class="abs heading svc-title" style="left:46px;top:530px">WALKING WORKSHOPS</h2>
  <p class="abs svc-text" style="left:46px;top:561px">Brightmoor Walking is an initiative aimed at getting people back into nature in the most gentlest of ways - by taking a walk with friends in the great outdoors. The concept is simple - schedule a walk outside, once a week with two or three other people. That's it. Sometimes the best things are the simplest and here's why this works.</p>
  <div class="btn btn--sm" style="left:46px;top:680px">Read more</div>
  <div class="photo photo--walk" role="img" aria-label="Person walking along a wooden boardwalk across moorland"></div>

  <div class="photo photo--bloom" role="img" aria-label="Pink cherry blossom in full bloom"></div>
  <h2 class="abs heading svc-title" style="left:329px;top:767px">RETREATS</h2>
  <p class="abs svc-text" style="left:329px;top:797px">Sometimes you just need to get away from it all. And that's where Brightmoor retreats come in. Our retreats are based at Hollyglen Cottage located at the foot of the Mourne Mountains in beautiful Northern Ireland. Typically 2/3 days that involve restoring your connection to the natural world in stunning surroundings.</p>
  <div class="btn btn--sm" style="left:328px;top:918px">Read more</div>

  <h2 class="abs heading svc-title" style="left:46px;top:993px">OUTDOOR COACHING</h2>
  <p class="abs svc-text" style="left:46px;top:1024px;line-height:19.5px">Only one thing better than coaching and that's coaching in the great outdoors. We believe that being out in nature gives you a greater sense of perspective when working through issues and figuring out life's path. We are part of nature, not apart from it. We are ofWe can provide copy for internal publications.</p>
  <div class="btn btn--sm" style="left:46px;top:1150px">Read more</div>
  <div class="photo photo--stream" role="img" aria-label="Child in a red coat and a small dog by a rocky woodland stream"></div>

  <div class="abs quote-band" role="img" aria-label="Woodland floor carpeted with bluebells">
    <p class="abs quote">“I had had a lot of thoughts about creating Brightmoor for a while. No real direction or goal but just an inclination to create a place to gather resources to gather thoughts and demonstrate how to enjoy the great outdoors to improve your life. What turned the thoughts of what to do from thoughts to action came from an unlikely event”</p>
    <p class="abs quote-by">-Ellis Markham to the Town Hall.</p>
  </div>

  <h3 class="abs signup-title" style="font-weight:400">Let'S Meet Up In Real Life To The Importance Of Nature For Good Health.</h3>
  <p class="abs signup-note">Sign up to be the first to know about In sit amet felis malesuada, feugiat purus eget, varius mi. Nulla lectus ante, consequat</p>
  <div class="abs signup-input">Enter address</div>
  <div class="btn btn--signup">Sign up</div>

  <footer class="abs footer">
    <div class="abs brand" style="left:46px;top:20px"><span class="brand-dot"></span>BRIGHTMOOR.</div>
    <p class="abs footer-addr">48 Fernhill Lane<br>Newcastle, BT33 0AB<br>(555) 555-5555</p>
    <p class="abs footer-copy">© 2020 Brightmoor. All rights reserved</p>
    <div class="abs footer-col" style="left:434px;top:24px"><h4>QUICKS LINKS</h4>Home<br>About Us<br>Services<br>Contact Us</div>
    <div class="abs footer-col" style="left:536px;top:24px"><h4>FOLLOW</h4>Leafnote<br>Pathlink<br>Moorpage</div>
  </footer>

  <div class="abs dim"></div>
  <div class="abs cookie-modal" role="dialog" aria-label="Cookie consent">
    <div class="abs cookie-art" role="img" aria-label="Illustration of a bitten chocolate chip cookie"></div>
    <div class="abs cookie-close">
      <svg width="6" height="6" viewBox="0 0 6 6"><path d="M1 1L5 5M5 1L1 5" stroke="#fff" stroke-width="1.4"/></svg>
    </div>
    <p class="abs cookie-text">Our websites uses cookies to ensure you get the best experience while you're here.</p>
    <div class="btn btn--okay">Okay</div>
    <p class="abs cookie-more">Learn more</p>
  </div>
</section>

</body>
</html>
```